5-6 page Website Design- Harbor Lantern Program, including 2 videos

We need an elegantly simple and beautiful website for the Harbor Lantern Program (HLP), a 6-month program for founders and leaders of startups who want to shift from Actors to Authors in their leadership.
At a minimum, the website will include:
Home Page
Program Description--Why Actor to Author?
Program Timeline and Structure
Testimonials and Past Clients (this page will include a testimonials video and text)
Team
FAQs
I'd like to see two versions of The Home Page/Landing Page:
1. Just an image with the words
If your startup is growing rapidly,
we can help you do the same.
HLP: The ACTOR to AUTHOR Shift
2. A place for a video describing the program
No payment integration on the website. Just information.
Startup founders and senior leaders

```html
<!DOCTYPE html>
<html lang="en">
<head>
<meta charset="utf-8">
<title>Harbor Lantern Program — Website Screens</title>
<link rel="stylesheet" href="https://fonts.googleapis.com/css2?family=Catamaran:wght@600;700;800&family=Lato:ital,wght@0,400;0,700;1,400&display=swap">
<style>
:root{
  --stage:#1f1f20;
  --blue:#1e7fd0;
  --blue-deep:#0d5bb0;
  --blue-hero:#2584d3;
  --blue-bright:#2b8fdc;
  --ink:#1b1b1b;
  --body:#333;
  --light:#f0f1f3;
  --white:#fff;
  --black:#000;
  --line:#d9dde2;
}
*{margin:0;padding:0;box-sizing:border-box}
html,body{width:1200px;height:2400px;overflow:hidden;background:var(--stage)}
body{position:relative;font-family:'Lato',sans-serif;color:var(--body)}
.screen{position:absolute;width:573px;overflow:hidden;background:var(--white)}
.abs{position:absolute}
.head-font{font-family:'Catamaran',sans-serif}

/* nav */
.nav{position:absolute;left:0;top:0;width:100%;height:48px;z-index:3}
.brand{position:absolute;left:48px;top:10px;display:flex;align-items:center;gap:5px}
.brand-dot{width:24px;height:24px;border-radius:50%;background:var(--white)}
.brand-name{font-family:'Catamaran',sans-serif;font-weight:600;font-size:7.4px;line-height:8px;color:var(--white);letter-spacing:.3px;border-left:1px solid var(--white);padding-left:3px}
.nav-links{position:absolute;left:165px;top:20px;display:flex;gap:16px;font-family:'Catamaran',sans-serif;font-weight:700;font-size:5.6px;color:var(--white);letter-spacing:.1px}

/* hero */
.hero{position:absolute;left:0;top:0;width:573px;height:306px;background:linear-gradient(180deg,#2c8ad6 0%,#1f79c9 100%)}
.hero-bg{position:absolute;inset:0;background:linear-gradient(120deg,rgba(20,95,170,.35),rgba(60,150,225,.15))}
.hero-circle{position:absolute;border-radius:50%}
.hero-copy{position:absolute;left:275px;top:117px;width:280px;color:var(--white)}
.hero-copy h1{font-family:'Catamaran',sans-serif;font-weight:800;font-size:18.6px;line-height:21px;text-transform:uppercase}
.hero-copy p{font-family:'Catamaran',sans-serif;font-weight:600;font-size:7px;margin-top:7px}
.btn-white{display:inline-block;margin-top:7px;width:86px;height:24px;border-radius:12px;background:var(--white);color:var(--blue-deep);font-family:'Catamaran',sans-serif;font-weight:800;font-size:6.6px;text-align:center;line-height:24px}
.btn-blue{position:absolute;height:24px;width:86px;border-radius:12px;background:var(--blue-deep);color:var(--white);font-family:'Catamaran',sans-serif;font-weight:800;font-size:6.6px;text-align:center;line-height:24px;left:50%;margin-left:-43px}

/* section titles */
.sec-title{position:absolute;left:0;width:100%;text-align:center;font-family:'Catamaran',sans-serif;font-weight:800;font-size:15px;color:var(--ink);text-transform:uppercase}
.sec-title::after{content:"";display:block;width:18px;height:2px;background:var(--blue);margin:3px auto 0}

/* why */
.why-quote{position:absolute;left:85px;width:403px;text-align:center;font-weight:700;font-size:6.4px;line-height:10.5px;color:var(--blue-deep)}
.why-body{position:absolute;left:80px;width:413px;text-align:center;font-size:5.2px;line-height:10.8px;color:var(--body)}

/* timeline */
.timeline-axis{position:absolute;left:65px;top:166px;width:445px;height:1px;background:var(--blue-deep)}
.timeline-axis::before{content:"";position:absolute;left:-3px;top:-2.5px;width:6px;height:6px;border-radius:50%;background:var(--blue-deep)}
.timeline-axis::after{content:"";position:absolute;right:-1px;top:-2.5px;border-left:5px solid var(--blue-deep);border-top:3px solid transparent;border-bottom:3px solid transparent}
.month{position:absolute;width:68px;height:68px;border-radius:50%;color:var(--white);font-family:'Catamaran',sans-serif;font-weight:800;font-size:11.5px;display:flex;align-items:center;justify-content:center}
.month::after{content:"";position:absolute;left:29px;border-left:5px solid transparent;border-right:5px solid transparent}
.month.up{background:var(--blue-deep)}
.month.up::after{bottom:-7px;border-top:9px solid var(--blue-deep)}
.month.down{background:var(--blue-bright)}
.month.down::after{top:-7px;border-bottom:9px solid var(--blue-bright)}
.step{position:absolute;width:86px;text-align:center;font-size:5.3px;line-height:11.3px;color:var(--ink)}

/* logic */
.logic-copy{position:absolute;left:61px;top:37px;width:218px;color:var(--white)}
.logic-copy h2{font-family:'Catamaran',sans-serif;font-weight:800;font-size:14.2px;line-height:21px;text-transform:uppercase}
.logic-copy .ask{font-weight:700;font-size:4.6px;margin-top:9px}
.logic-copy h3{font-family:'Catamaran',sans-serif;font-weight:600;font-size:9.3px;margin-top:5px}
.logic-copy p{font-size:5.4px;line-height:11.3px;margin:4px 0 0 12px}

/* testimonials */
.testi-copy{position:absolute;left:296px;top:69px;width:213px}
.testi-copy h2{font-family:'Catamaran',sans-serif;font-weight:800;font-size:13.4px;color:var(--ink)}
.testi-copy h2::after{content:"";display:block;width:16px;height:2px;background:var(--blue);margin-top:3px}
.testi-copy .quote{font-style:italic;font-size:4.8px;line-height:11.3px;margin-top:9px;text-align:justify;color:var(--ink)}
.testi-copy .who{font-family:'Catamaran',sans-serif;font-weight:700;font-size:10px;color:var(--blue);margin-top:2px}
.testi-copy .role{font-size:5.2px}
.clients-head{position:absolute;left:63px;top:217px;width:447px;border-bottom:1px solid var(--blue);height:15px;font-family:'Catamaran',sans-serif;font-weight:800;font-size:9.3px;color:var(--ink)}
.clients-head .arrows{position:absolute;right:2px;top:-1px;font-size:10px;font-weight:600;letter-spacing:6px}
.client-row{position:absolute;left:63px;top:245px;width:447px;display:flex;gap:5px}
.client{flex:1;height:30px;background:var(--white);border:1px solid var(--line);display:flex;align-items:center;justify-content:center;gap:3px;font-weight:700;font-size:5.4px;color:var(--blue-deep)}
.client i{display:block;width:6px;height:6px;border-radius:50%;background:var(--blue-deep)}

/* team */
.team-grid{position:absolute;left:63px;top:72px;width:446px;height:191px;display:grid;grid-template-columns:repeat(4,1fr);grid-template-rows:1fr 1fr}
.member{color:var(--white);text-align:center;padding:10px 9px 0}
.member.sky{background:var(--blue-bright)}
.member.navy{background:var(--blue-deep)}
.member h4{font-family:'Catamaran',sans-serif;font-weight:800;font-size:8.6px}
.member p{font-size:5.1px;line-height:11.2px;margin-top:1px}
.socials{display:flex;justify-content:center;gap:9px;margin-top:6px}
.socials span{width:5px;height:5px;border-radius:50%;background:var(--white)}
.portrait{background:linear-gradient(180deg,#eef0f2,#dfe3e8)}

/* faq */
.faq-item{position:absolute;left:95px;width:382px;background:var(--white);border:1px solid var(--line);border-radius:3px;box-shadow:0 1px 4px rgba(0,0,0,.12)}
.faq-q{height:34px;padding:0 11px;display:flex;align-items:center;justify-content:space-between;font-family:'Catamaran',sans-serif;font-weight:700;font-size:6.4px;color:var(--ink)}
.faq-q::after{content:"";border-left:2.5px solid transparent;border-right:2.5px solid transparent;border-top:3px solid var(--ink)}
.faq-item.open .faq-q{height:22px;color:var(--blue-deep)}
.faq-item.open .faq-q::after{border-top:none;border-bottom:3px solid var(--ink)}
.faq-a{padding:0 18px 12px;font-size:5.2px;line-height:11.3px;color:var(--body)}

/* footer */
.site-footer{background:var(--black);color:var(--white);text-align:center}
.foot-brand{position:absolute;left:50%;top:37px;transform:translateX(-50%);display:flex;align-items:center;gap:6px}
.foot-brand .brand-dot{width:38px;height:38px;background:var(--blue)}
.foot-brand .brand-name{font-size:10.6px;line-height:11px;color:var(--blue);border-color:var(--blue);padding-left:5px;text-align:left}
.foot-nav{position:absolute;left:0;width:100%;top:98px;display:flex;justify-content:center;gap:16px;font-family:'Catamaran',sans-serif;font-weight:700;font-size:5.6px}
.foot-contact{position:absolute;left:0;width:100%;top:118px;display:flex;justify-content:center;gap:22px;font-size:5.6px;align-items:center}
.foot-contact span{display:flex;align-items:center;gap:5px}
.foot-contact svg{width:17px;height:17px}
.foot-copy{position:absolute;left:0;width:100%;top:147px;font-weight:700;font-size:5.4px}
.foot-copy b{color:var(--blue);font-weight:700}
</style>
</head>
<body>

<!-- Screen A: landing, image version -->
<section class="screen" style="left:16px;top:13px;height:306px">
  <div class="hero">
    <div class="hero-bg" role="img" aria-label="Blurred photo of a team meeting in an office, tinted blue"></div>
    <div class="hero-circle" role="img" aria-label="Circular photo of colleagues talking at a meeting table" style="left:71px;top:84px;width:204px;height:204px;background:radial-gradient(circle at 45% 40%,#e9eef2 0%,#aebdca 45%,#3b87cc 100%)"></div>
    <nav class="nav">
      <div class="brand"><span class="brand-dot"></span><span class="brand-name">HARBOR<br>LANTERN<br>PROGRAM</span></div>
      <div class="nav-links"><span>HOME</span><span>WHY ACTOR TO AUTHOR?</span><span>PROGRAM TIMELINE AND STRUCTURE</span><span>TESTIMONIALS</span><span>TEAM</span><span>FAQ</span></div>
    </nav>
    <div class="hero-copy">
      <h1>If your startup is growing rapidly,we can help you do the same.</h1>
      <p>HLP: THE ACTOR TO AUTHOR SHIFT</p>
      <span class="btn-white">GET STARTED</span>
    </div>
  </div>
</section>

<!-- Screen B: landing, video version -->
<section class="screen" style="left:16px;top:337px;height:558px">
  <div class="hero">
    <div class="hero-bg" role="img" aria-label="Mountain summit landscape with a hiker, tinted blue"></div>
    <div class="hero-circle" role="img" aria-label="Program video: circular sunset mountain scene" style="left:176px;top:42px;width:220px;height:220px;background:radial-gradient(circle at 50% 35%,#f6c77a 0%,#e58a4a 35%,#6a5a68 65%,#2f4d5e 100%)"></div>
    <svg class="abs" style="left:271px;top:137px" width="30" height="30" viewBox="0 0 30 30" aria-label="Play video"><circle cx="15" cy="15" r="14" fill="#fff" opacity=".9"/><path d="M12 9 L21 15 L12 21 Z" fill="#1e7fd0"/></svg>
    <nav class="nav">
      <div class="brand"><span class="brand-dot"></span><span class="brand-name">HARBOR<br>LANTERN<br>PROGRAM</span></div>
      <div class="nav-links"><span>HOME</span><span>WHY ACTOR TO AUTHOR?</span><span>PROGRAM TIMELINE AND STRUCTURE</span><span>TESTIMONIALS</span><span>TEAM</span><span>FAQ</span></div>
    </nav>
  </div>
  <div class="abs" style="left:0;top:306px;width:573px;height:221px">
    <h2 class="sec-title" style="top:38px">Why Actor to Author?</h2>
    <p class="why-quote" style="top:74px">“If you want to be busy and anxious, practice busy anxiousness. If you want to be calm and centered, practice it. It’s as simple as that.” (Mara Lindqvist, Westbrook College mindfulness teacher and researcher)</p>
    <p class="why-body" style="top:98px">Well thanks Mara, sounds pretty simple...but what about when I’ve got 11 back-to-back meetings, a board meeting to prepare for with investors who have sky-high expectations, 6 new hires to onboard and 16 more to find, and–not least–a product to improve for the customers we are trying to serve and retain–only to wake up, rinse (maybe) and repeat tomorrow?? (We didn’t even mention the team chat messages mounting in the background.) How could I possibly exit “busy anxiousness” and practice calm centeredness amidst this chaos? (Notice what you feel just reading that–does your body tighten a bit?) Calm sounds nice–for vacation! I want results.</p>
    <span class="btn-blue" style="top:166px">LEARN MORE</span>
  </div>
  <footer class="site-footer abs" style="left:0;top:527px;width:573px;height:31px;font-size:5px;line-height:31px">© copyrights 2022 Harbor Lantern Program &nbsp;|&nbsp; All Rights Reserved</footer>
</section>

<!-- Screen C: full home page -->
<section class="screen" style="left:604px;top:13px;height:2356px">

  <div class="hero">
    <div class="hero-bg" role="img" aria-label="Calm lake at dawn, tinted blue"></div>
    <div class="hero-circle" role="img" aria-label="Circular photo of a woman meditating on a lakeside dock" style="left:72px;top:84px;width:204px;height:204px;background:radial-gradient(circle at 50% 40%,#d9e6f0 0%,#7fb1dd 45%,#2a7cc8 100%)"></div>
    <nav class="nav">
      <div class="brand"><span class="brand-dot"></span><span class="brand-name">HARBOR<br>LANTERN<br>PROGRAM</span></div>
      <div class="nav-links"><span>HOME</span><span>WHY ACTOR TO AUTHOR?</span><span>PROGRAM TIMELINE AND STRUCTURE</span><span>TESTIMONIALS</span><span>TEAM</span><span>FAQ</span></div>
    </nav>
    <div class="hero-copy">
      <h1>If your startup is growing rapidly,we can help you do the same.</h1>
      <p>HLP: THE ACTOR TO AUTHOR SHIFT</p>
      <span class="btn-white">GET STARTED</span>
    </div>
  </div>

  <div class="abs" style="left:0;top:306px;width:573px;height:236px">
    <h2 class="sec-title" style="top:40px">Why Actor to Author?</h2>
    <p class="why-quote" style="top:76px">“If you want to be busy and anxious, practice busy anxiousness. If you want to be calm and centered, practice it. It’s as simple as that.” (Mara Lindqvist, Westbrook College mindfulness teacher and researcher)</p>
    <p class="why-body" style="top:100px">Well thanks Mara, sounds pretty simple...but what about when I’ve got 11 back-to-back meetings, a board meeting to prepare for with investors who have sky-high expectations, 6 new hires to onboard and 16 more to find, and–not least–a product to improve for the customers we are trying to serve and retain–only to wake up, rinse (maybe) and repeat tomorrow?? (We didn’t even mention the team chat messages mounting in the background.) How could I possibly exit “busy anxiousness” and practice calm centeredness amidst this chaos? (Notice what you feel just reading that–does your body tighten a bit?) Calm sounds nice–for vacation! I want results.</p>
    <span class="btn-blue" style="top:166px">LEARN MORE</span>
  </div>

  <div class="abs" style="left:0;top:542px;width:573px;height:338px;background:var(--light)">
    <h2 class="sec-title" style="top:37px">Program Timeline and Structure</h2>
    <div class="step" style="left:55px;top:108px">Week 1: Kickoff Orientation Workshop<br>Week 2: 1on1 Exec Coaching Session<br>Week 3: Workshop</div>
    <div class="month up" style="left:140px;top:81px">MONTH 2</div>
    <div class="step" style="left:206px;top:108px">Week 2: 1on1 Exec Coaching Session<br>Week 4: Workshop</div>
    <div class="month up" style="left:291px;top:81px">MONTH 4</div>
    <div class="step" style="left:357px;top:93px">Week 1: 2nd Retreat (“Leading Others, Leading Relationships”)<br>Week 2: 1on1 Exec Coaching Session<br>Week 4: Workshop</div>
    <div class="month up" style="left:440px;top:81px">MONTH 6</div>
    <div class="timeline-axis"></div>
    <div class="month down" style="left:66px;top:179px">MONTH 1</div>
    <div class="step" style="left:132px;top:173px">Week 1: 1st Retreat (“Leading Yourself”)<br>Week 2: 1on1 Exec Coaching Session<br>Week 4: Workshop</div>
    <div class="month down" style="left:215px;top:179px">MONTH 3</div>
    <div class="step" style="left:282px;top:173px">Week 2: 1on1 Exec Coaching Session</div>
    <div class="month down" style="left:366px;top:179px">MONTH 5</div>
    <div class="step" style="left:430px;top:173px">Week 2: 1on1 Exec Coaching Session<br>Week 4: Concluding Workshop<br>Week 5: Concluding 1on1 Exec Coaching Session</div>
    <span class="btn-blue" style="top:278px">VIEW SUMMARY</span>
  </div>

  <div class="abs" style="left:0;top:880px;width:573px;height:265px;background:var(--blue-deep);overflow:hidden">
    <div class="abs" role="img" aria-label="Faint photo of a team at work, tinted blue" style="inset:0;background:linear-gradient(90deg,rgba(13,91,176,1) 0%,rgba(40,120,200,.6) 60%,rgba(13,91,176,1) 100%)"></div>
    <div class="abs" role="img" aria-label="Large circular illustration area" style="left:300px;top:-7px;width:270px;height:270px;border-radius:50%;background:var(--white)"></div>
    <div class="logic-copy">
      <h2>The logic behind<br>the structure</h2>
      <p class="ask" style="margin:9px 0 0">Why combine both group format (retreats/workshops) and 1on1 exec coaching?</p>
      <h3>1 . Why retreats? Immersion!</h3>
      <p>The retreat environment creates an immersive experience, co-created by the group. The sharp distinction from the fast pace of everyday startup life helps participants stand outside their everyday habits and evaluate which ones they want to change. Furthermore, just like in learning a language, immersion is the most powerful context for learning and ingraining new habits.</p>
      <span class="btn-white" style="margin-top:9px">LEARN MORE</span>
    </div>
  </div>

  <div class="abs" style="left:0;top:1145px;width:573px;height:319px;background:var(--light)">
    <div class="abs" role="img" aria-label="Testimonial video: smiling team members around a laptop" style="left:65px;top:56px;width:218px;height:140px;background:linear-gradient(135deg,#c9d2d8,#8d9aa4 55%,#5c6870)"></div>
    <svg class="abs" style="left:160px;top:112px" width="28" height="28" viewBox="0 0 28 28" aria-label="Play video"><circle cx="14" cy="14" r="13" fill="#fff"/><path d="M11 8 L20 14 L11 20 Z" fill="#1b1b1b"/></svg>
    <div class="testi-copy">
      <h2>OUR TESTIMONIALS</h2>
      <p class="quote">Lorem ipsum dolor sit amet, consectetur adipiscing elit, sed do eiusmod tempor incididunt ut labore et dolore magna aliqua. Ut enim ad minim veniam, quis nostrud exercitation ullamco laboris nisi ut aliquip ex ea commodo consequat. Duis aute irure dolor in reprehenderit in voluptate velit esse cillum dolore eu fugiat nulla pariatur. Excepteur sint occaecat cupidatat non proident, sunt in culpa qui officia deserunt mollit anim id est laborumSed ut perspiciatis unde omnis.</p>
      <p class="who">John Deo</p>
      <p class="role">Lorem ipsum dolor sit</p>
    </div>
    <div class="clients-head">OUR CLIENTS<span class="arrows">‹›</span></div>
    <div class="client-row">
      <div class="client"><i></i>Northwind</div>
      <div class="client"><i></i>Ridgeline</div>
      <div class="client"><i></i>Brightform</div>
      <div class="client"><i></i>Tandem</div>
      <div class="client"><i></i>Looplight</div>
      <div class="client"><i></i>Clearwave</div>
    </div>
  </div>

  <div class="abs" style="left:0;top:1464px;width:573px;height:300px;background:var(--white)">
    <h2 class="sec-title" style="top:36px">Meet Our Team</h2>
    <div class="team-grid">
      <div class="member sky"><h4>JOHN DOE</h4><p>Lorem ipsum dolor sit amet, consectetur adipiscing elit, sed do eiusmod tempor incididunt ut labore et dolore magna aliqua.</p><div class="socials" aria-label="Social links"><span></span><span></span><span></span><span></span></div></div>
      <div class="portrait" role="img" aria-label="Portrait of a team member with glasses"></div>
      <div class="member sky"><h4>JOHN DOE</h4><p>Lorem ipsum dolor sit amet, consectetur adipiscing elit, sed do eiusmod tempor incididunt ut labore et dolore magna aliqua.</p><div class="socials" aria-label="Social links"><span></span><span></span><span></span><span></span></div></div>
      <div class="portrait" role="img" aria-label="Portrait of a smiling team member"></div>
      <div class="portrait" role="img" aria-label="Portrait of a team member in a denim shirt"></div>
      <div class="member navy"><h4>JENIFFER</h4><p>Lorem ipsum dolor sit amet, consectetur adipiscing elit, sed do eiusmod tempor incididunt ut labore et dolore magna aliqua.</p><div class="socials" aria-label="Social links"><span></span><span></span><span></span><span></span></div></div>
      <div class="portrait" role="img" aria-label="Portrait of a team member in a dark shirt"></div>
      <div class="member navy"><h4>JENIFFER</h4><p>Lorem ipsum dolor sit amet, consectetur adipiscing elit, sed do eiusmod tempor incididunt ut labore et dolore magna aliqua.</p><div class="socials" aria-label="Social links"><span></span><span></span><span></span><span></span></div></div>
    </div>
  </div>

  <div class="abs" style="left:0;top:1764px;width:573px;height:418px;background:var(--light)">
    <h2 class="sec-title" style="top:40px">Frequently Asked Question</h2>
    <div class="faq-item open" style="top:73px">
      <div class="faq-q">1. LOREM IPSUM DOLOR SIT AMET CONSECTETUR ADIPISCING ELIT ?</div>
      <p class="faq-a">Every year, billions of login details from hundreds of websites are taken in hacker attacks. These stolen email addresses, passwords, and other account details are then exposed on the dark web or sold on the black market, where criminals pay to gain access to your sensitive data. Companies or organizations you do business with can also leak or publish their users’ sensitive information by accident.If criminals get a hold of one of your accounts, they can potentially impersonate you, message your contacts, access your cloud storage, steal your money, and even jump to your other accounts. That’s why we take password safety so seriously.</p>
    </div>
    <div class="faq-item" style="top:186px"><div class="faq-q">2. LOREM IPSUM DOLOR SIT AMET CONSECTETUR ADIPISCING ELIT?</div></div>
    <div class="faq-item" style="top:224px"><div class="faq-q">3. LOREM IPSUM DOLOR SIT AMET CONSECTETUR ADIPISCING ELIT?</div></div>
    <div class="faq-item" style="top:261px"><div class="faq-q">4. LOREM IPSUM DOLOR SIT AMET CONSECTETUR ADIPISCING ELIT?</div></div>
    <div class="faq-item" style="top:298px"><div class="faq-q">5. LOREM IPSUM DOLOR SIT AMET CONSECTETUR ADIPISCING ELIT?</div></div>
    <div class="faq-item" style="top:335px"><div class="faq-q">6. LOREM IPSUM DOLOR SIT AMET CONSECTETUR ADIPISCING ELIT?</div></div>
  </div>

  <footer class="site-footer abs" style="left:0;top:2182px;width:573px;height:174px">
    <div class="foot-brand"><span class="brand-dot"></span><span class="brand-name">HARBOR<br>LANTERN<br>PROGRAM</span></div>
    <div class="foot-nav"><span>HOME</span><span>WHY ACTOR TO AUTHOR?</span><span>PROGRAM TIMELINE AND STRUCTURE</span><span>TESTIMONIALS</span><span>TEAM</span><span>FAQ</span></div>
    <div class="foot-contact">
      <span><svg viewBox="0 0 20 20"><circle cx="10" cy="10" r="10" fill="#fff"/><path d="M10 4a4 4 0 0 0-4 4c0 3 4 8 4 8s4-5 4-8a4 4 0 0 0-4-4z" fill="#1e7fd0"/><circle cx="10" cy="8" r="1.5" fill="#fff"/></svg>123 Lorem ipsum dolor sit amet</span>
      <span><svg viewBox="0 0 20 20"><circle cx="10" cy="10" r="10" fill="#fff"/><path d="M6.5 5.5l2 0 1 2.5-1.3 1a6 6 0 0 0 2.8 2.8l1-1.3 2.5 1 0 2a1 1 0 0 1-1 1A8 8 0 0 1 5.5 6.5a1 1 0 0 1 1-1z" fill="#1e7fd0"/></svg>+1 555 014 2200</span>
      <span><svg viewBox="0 0 20 20"><circle cx="10" cy="10" r="10" fill="#fff"/><rect x="5" y="6.5" width="10" height="7" rx="1" fill="#1e7fd0"/><path d="M5.5 7l4.5 3.5L14.5 7" stroke="#fff" stroke-width=".8" fill="none"/></svg>info@harborlanternprogram.example</span>
    </div>
    <p class="foot-copy">© COPYRIGHTS 2022 <b>HARBOR LANTERN PROGRAM</b> | ALL RIGHTS RESERVED</p>
  </footer>
</section>

</body>
</html>
```